Design a New Business Card for Our Company

We are looking for fresh, unique, and a modern business card that reflects our roots as digital marketing agency focused on SEM.

Industry/Entity Type

Marketing

Contact Information for Business Card

looking for very unique out of the box designs. clean and modern that compliments our logo

Requirements
Must have
• colors should match our logo
• Front should have name, address, email, and phone/fax of the person, phone/fax are the same number
• back should have our url

```html
<!DOCTYPE html>
<html lang="en">
<head>
<meta charset="utf-8">
<title>Clearpath Solutions — Business Card</title>
<link rel="stylesheet" href="https://fonts.googleapis.com/css2?family=Arimo:wght@400;700&display=swap">
<style>
  :root {
    --stage: #e9ebee;
    --card-white: #ffffff;
    --card-grey: #eceeef;
    --ink-grey: #8f9295;
    --ink-soft: #a4a7aa;
    --brand-blue: #3f86c4;
    --icon-blue: #5a9bd0;
    --back-light: #86c3e0;
    --back-mid: #5d9dcb;
    --back-dark: #3c74aa;
    --dot-grey: rgba(190,191,193,0.55);
    --dot-blue: rgba(104,164,214,0.75);
  }
  * { box-sizing: border-box; margin: 0; padding: 0; }
  html, body { width: 1200px; height: 780px; overflow: hidden; }
  body {
    background: var(--stage);
    font-family: "Arimo", Arial, sans-serif;
    display: flex;
    align-items: center;
    justify-content: center;
    gap: 40px;
  }
  .card {
    position: relative;
    width: 540px;
    height: 309px;
    border-radius: 3px;
    overflow: hidden;
    box-shadow: 0 6px 18px rgba(0,0,0,0.16);
  }

  /* Front */
  .card-front {
    background: linear-gradient(200deg, var(--card-white) 35%, var(--card-grey) 100%);
  }
  .front-decoration {
    position: absolute;
    inset: 0;
    background:
      radial-gradient(ellipse 170px 200px at 100% 0%, var(--dot-blue) 0%, rgba(104,164,214,0.3) 50%, rgba(104,164,214,0) 100%),
      radial-gradient(ellipse 260px 230px at 85% 0%, var(--dot-grey) 0%, rgba(190,191,193,0.25) 55%, rgba(190,191,193,0) 100%);
  }
  .brand {
    position: absolute;
    left: 34px;
    top: 104px;
    display: flex;
    align-items: center;
    gap: 12px;
  }
  .brand-dot {
    width: 30px;
    height: 30px;
    border-radius: 50%;
    background: var(--brand-blue);
  }
  .brand-name {
    font-size: 30px;
    font-weight: 700;
    color: var(--ink-grey);
    letter-spacing: -0.5px;
  }
  .person {
    position: absolute;
    left: 34px;
    top: 168px;
  }
  .person-name {
    font-size: 15px;
    font-weight: 700;
    color: var(--brand-blue);
    text-transform: uppercase;
    letter-spacing: 0.3px;
  }
  .person-title {
    font-size: 12px;
    color: var(--ink-grey);
    margin-top: 2px;
  }
  .contact {
    position: absolute;
    left: 200px;
    top: 168px;
    font-size: 12px;
    line-height: 17px;
    color: var(--ink-soft);
    list-style: none;
  }
  .contact-line {
    display: flex;
    align-items: center;
    gap: 6px;
  }
  .contact-icon {
    width: 13px;
    height: 13px;
    flex: none;
  }

  /* Back */
  .card-back {
    background: radial-gradient(ellipse at 50% 50%, var(--back-light) 0%, var(--back-mid) 55%, var(--back-dark) 100%);
    display: flex;
    align-items: center;
    justify-content: center;
  }
  .back-url {
    color: #ffffff;
    font-size: 20px;
    letter-spacing: 0.3px;
  }
</style>
</head>
<body>
  <section class="card card-front" aria-label="Business card front">
    <div class="front-decoration" role="img" aria-label="Decorative field of grey and blue circles"></div>

    <div class="brand">
      <span class="brand-dot"></span>
      <span class="brand-name">clearpath solutions</span>
    </div>

    <div class="person">
      <p class="person-name">Dana Rowe</p>
      <p class="person-title">Manager</p>
    </div>

    <ul class="contact">
      <li class="contact-line">Your Address,2nd Ste</li>
      <li class="contact-line">Lakeview, Ohio 1234</li>
      <li class="contact-line">
        <svg class="contact-icon" viewBox="0 0 13 13" aria-hidden="true"><rect width="13" height="13" fill="var(--icon-blue)"/><path d="M4 3h2l.6 2-1.2.8a6 6 0 0 0 2 2l.8-1.2 2 .6v2c-3.6.3-6.5-2.6-6.2-6.2z" fill="#fff"/></svg>
        123 456 7890
      </li>
      <li class="contact-line">
        <svg class="contact-icon" viewBox="0 0 13 13" aria-hidden="true"><rect width="13" height="13" fill="var(--icon-blue)"/><rect x="3.5" y="2.5" width="6" height="3" fill="#fff"/><rect x="2.5" y="5.5" width="8" height="4" fill="#fff"/><rect x="4" y="8" width="5" height="2.5" fill="var(--icon-blue)" stroke="#fff" stroke-width=".8"/></svg>
        123 456 7890
      </li>
      <li class="contact-line">
        <svg class="contact-icon" viewBox="0 0 13 13" aria-hidden="true"><rect width="13" height="13" fill="var(--icon-blue)"/><rect x="2.5" y="3.5" width="8" height="6" fill="#fff"/><path d="M2.5 3.5l4 3.2 4-3.2" fill="none" stroke="var(--icon-blue)" stroke-width=".9"/></svg>
        your@yourcompany.com
      </li>
    </ul>
  </section>

  <section class="card card-back" aria-label="Business card back">
    <p class="back-url">www.yourwebsite.com</p>
  </section>
</body>
</html>
```